Aunt Roula's Bakery

I am about to create a luxury boutique that specializes in cake baking and cupcake
and ready for parties and special events and order delivery
the logo has already made

Boutique

Email:auntroulasbakery@mailbox-example.net
Instagram: aunt_roula_bakery
Twitter: xxxxxxx
WhatsApp: xxxxxxx

Requirements
Must have
• luxury design

```html
<!DOCTYPE html>
<html lang="en">
<head>
<meta charset="utf-8">
<title>Aunt Roula's Bakery — Business Card</title>
<link rel="stylesheet" href="https://fonts.googleapis.com/css2?family=Open+Sans:wght@400;700&display=swap">
<style>
  :root {
    --backdrop: #e7e4df;
    --card-white: #f8f8f6;
    --band-light: #aaa9a4;
    --band-dark: #91908b;
    --ink-light: #fbfbfa;
    --accent-pink: #e48aa5;
    --ornament-fill: #ebeae7;
    --frame-fill: #f0efec;
    --frame-edge: #dcdbd7;
    --logo-grey: #8c8b87;
  }
  * { margin: 0; padding: 0; box-sizing: border-box; }
  html, body {
    width: 1200px;
    height: 1022px;
    overflow: hidden;
    background: var(--backdrop);
    font-family: "Open Sans", Arial, sans-serif;
  }
  .business-card {
    position: absolute;
    left: 90px;
    top: 219px;
    width: 1020px;
    height: 583px;
    background: var(--card-white);
    box-shadow: 0 10px 30px rgba(0,0,0,0.12);
    overflow: hidden;
  }
  .band {
    position: absolute;
    background: linear-gradient(180deg, var(--band-light), var(--band-dark));
  }
  .band--owner {
    left: 24px;
    top: 28px;
    width: 610px;
    height: 160px;
  }
  .band--contact {
    right: 24px;
    bottom: 28px;
    width: 610px;
    height: 176px;
  }
  .owner-name {
    position: absolute;
    left: 40px;
    top: 62px;
    color: var(--ink-light);
    font-weight: 700;
    font-size: 38px;
    letter-spacing: 1px;
    line-height: 1;
  }
  .owner-role {
    position: absolute;
    left: 42px;
    top: 110px;
    color: var(--accent-pink);
    font-weight: 400;
    font-size: 19px;
    letter-spacing: 1px;
    line-height: 1;
  }
  .contact-list {
    position: absolute;
    left: 32px;
    top: 20px;
    list-style: none;
  }
  .contact-item {
    display: flex;
    align-items: center;
    gap: 14px;
    height: 34px;
    color: var(--ink-light);
    font-size: 22px;
    font-weight: 400;
    white-space: nowrap;
  }
  .contact-marker {
    width: 16px;
    height: 16px;
    border: 2px solid var(--accent-pink);
    border-radius: 3px;
    flex: none;
  }
  .ornament {
    position: absolute;
    height: 44px;
    width: 220px;
    border-radius: 22px;
    background: var(--ornament-fill);
  }
  .ornament--top-right { left: 700px; top: 44px; }
  .ornament--bottom-left { left: 90px; top: 496px; }
  .logo-frame {
    position: absolute;
    left: 300px;
    top: 208px;
    width: 420px;
    height: 166px;
    border-radius: 83px;
    background: var(--frame-fill);
    border: 1px solid var(--frame-edge);
  }
  .logo-lockup {
    position: absolute;
    left: 300px;
    top: 238px;
    width: 420px;
    display: flex;
    flex-direction: column;
    align-items: center;
    gap: 14px;
  }
  .logo-dot {
    width: 36px;
    height: 36px;
    border-radius: 50%;
    background: var(--accent-pink);
  }
  .logo-name {
    color: var(--logo-grey);
    font-size: 24px;
    font-weight: 400;
    letter-spacing: 2px;
    text-transform: uppercase;
    white-space: nowrap;
  }
</style>
</head>
<body>
  <div class="business-card">
    <div class="band band--owner">
      <div class="owner-name">AUNT ROULA</div>
      <div class="owner-role">OWNER</div>
    </div>

    <div class="ornament ornament--top-right" role="img" aria-label="Grey scrollwork flourish"></div>
    <div class="ornament ornament--bottom-left" role="img" aria-label="Grey scrollwork flourish"></div>

    <div class="logo-frame" role="img" aria-label="Ornamental scrollwork frame around the bakery name"></div>
    <div class="logo-lockup">
      <div class="logo-dot"></div>
      <div class="logo-name">Aunt Roula's Bakery</div>
    </div>

    <div class="band band--contact">
      <ul class="contact-list">
        <li class="contact-item"><span class="contact-marker"></span>xxxxxxx</li>
        <li class="contact-item"><span class="contact-marker"></span>xxxxxxx</li>
        <li class="contact-item"><span class="contact-marker"></span>aunt_roula_bakery</li>
        <li class="contact-item"><span class="contact-marker"></span>auntroulasbakery@mailbox-example.net</li>
      </ul>
    </div>
  </div>
</body>
</html>
```